Quorva - corporate Business Card

We need a good look and innovative business card for a new start up company based in Los Angeles called "Quorva". We are in a payment business, including payment card, app, and ewallet. We are expert in online payment and Card not present (CNP) transaction.
We need an innovative, modern business card.

Our logo font is Aero Matics

Target Market(s)

Startup - Bank - Online Payment - Card Manufacturing

Industry/Entity Type

Startup

Contact Information for Business Card

phone: 555 014 7396 - Address: 4172 Marlowe blvd, Alderway, WA 98299

Requirements
Must have
• Message: innovative, professional, expert, high tech, trust, online payment expert, security
Nice to have
• no comment
Should not have
• no Comment

```html
<!DOCTYPE html>
<html lang="en">
<head>
<meta charset="utf-8">
<title>Quorva – Business Card</title>
<link rel="stylesheet" href="https://fonts.googleapis.com/css2?family=Open+Sans:wght@400;600;700&display=swap">
<style>
  :root {
    --brand-red: #b71f2e;
    --card-white: #ffffff;
    --backdrop: #e9e5e0;
    --ink-grey: #4a4a4a;
    --text-font: "Open Sans", Arial, sans-serif;
  }
  * { box-sizing: border-box; margin: 0; padding: 0; }
  html, body {
    width: 1200px;
    height: 987px;
    overflow: hidden;
    background: var(--backdrop);
    font-family: var(--text-font);
  }
  .canvas { position: relative; width: 1200px; height: 987px; }

  .card {
    position: absolute;
    left: 292px;
    width: 616px;
    height: 351px;
    box-shadow: 0 3px 10px rgba(0,0,0,0.18);
  }

  /* Front */
  .card--front { top: 130px; background: var(--brand-red); color: var(--card-white); }
  .front__block {
    position: absolute;
    left: 0; top: 53px;
    width: 265px; height: 246px;
    background: var(--card-white);
  }
  .front__info { position: absolute; left: 342px; top: 56px; }
  .front__brand { font-size: 42px; font-weight: 600; line-height: 1; letter-spacing: 0.5px; }
  .front__name { margin-top: 20px; font-size: 21px; font-weight: 600; line-height: 1.1; }
  .front__title { font-size: 16.5px; line-height: 1.4; }
  .front__address { margin-top: 10px; font-size: 16.5px; line-height: 1.38; font-style: normal; }
  .front__contacts { margin-top: 5px; list-style: none; font-size: 16.5px; line-height: 1.42; }
  .front__contacts li { display: flex; align-items: center; gap: 10px; }
  .front__contacts svg { width: 15px; height: 15px; fill: var(--card-white); flex: none; }

  /* Back */
  .card--back { top: 505px; background: var(--card-white); }
  .back__mark {
    position: absolute;
    left: 116px; top: 118px;
    width: 114px; height: 114px;
    border-radius: 50%;
    background: var(--brand-red);
  }
  .back__brand {
    position: absolute;
    left: 246px; top: 128px;
    font-size: 72px; font-weight: 600;
    line-height: 1;
    color: var(--brand-red);
    letter-spacing: 1px;
  }
  .back__web {
    position: absolute;
    left: 0; right: 0; top: 290px;
    text-align: center;
    font-size: 16px;
    letter-spacing: 8px;
    color: var(--ink-grey);
  }
</style>
</head>
<body>
<main class="canvas">
  <section class="card card--front">
    <div class="front__block"></div>
    <div class="front__info">
      <div class="front__brand">Quorva</div>
      <div class="front__name">DANIEL REYES</div>
      <div class="front__title">CEO&amp;Founder</div>
      <address class="front__address">
        4172 Marlowe blvd<br>Alderway, WA 98299
      </address>
      <ul class="front__contacts">
        <li>
          <svg viewBox="0 0 16 16" aria-hidden="true"><path d="M3.6 1.2l2.3 2.7-1.4 1.7c.9 2 2.6 3.7 4.6 4.6l1.7-1.4 2.7 2.3-1.3 2.4C7 13.6 2.4 9 1.2 3.6z"/></svg>
          555 014 7396
        </li>
        <li>
          <svg viewBox="0 0 16 16" aria-hidden="true"><path d="M1 3.5h14v9H1z M1.8 4.2L8 9l6.2-4.8" fill="none" stroke="#fff" stroke-width="1.3"/></svg>
          daniel@quorva.com
        </li>
        <li>
          <svg viewBox="0 0 16 16" aria-hidden="true"><circle cx="8" cy="8" r="7"/><path d="M4 4.5c1.5.2 2.4 1 2 2.3-.4 1-1.8.8-1.6 2.3.2 1.1 1.4 1.5 1.3 3.4M10 2.4c-.5 1.2.3 2 1.5 2.2 1 .2 1.4 1.3.9 2.3-.5 1-1.9.8-1.9 2.3 0 1 .7 1.4.8 2.8" fill="none" stroke="#b71f2e" stroke-width="1.3"/></svg>
          www.quorva.com
        </li>
      </ul>
    </div>
  </section>

  <section class="card card--back">
    <div class="back__mark"></div>
    <div class="back__brand">Quorva</div>
    <div class="back__web">www.quorva.com</div>
  </section>
</main>
</body>
</html>
```